Web design for sitter site

We will be launching a sitter site in the coming months that focuses on sitters for children. The name of this site will be NestWatch.com
We will need:
1. main page design
2. site logo designed
3. subpages as well for the look of people's profiles, and job listings, etc (see links below)
We only need the design, photos, font files, etc. We do not need this site coded (no html), a ps job is fine.
Some competing sites in the space include - tendlane.com and brio.com
http://www.pebble-keeper.example/images/profile1.jpg
http://marrowbooks.example/wp-content/uploads/2013/09/brio-review.png
http://www.quillmont.example/hr/photos/tend_lane2.jpg
Thanks for your interest!
Mothers of children, mainly women
Online

```html
<!DOCTYPE html>
<html lang="en">
<head>
<meta charset="utf-8">
<title>NestWatch – Trusted Sitters</title>
<link href="https://fonts.googleapis.com/css2?family=Open+Sans:wght@400;600;700&display=swap" rel="stylesheet">
<style>
:root{
  --brand:#3338dc;
  --brand-soft:#8a8ee6;
  --ink:#333;
  --muted:#777;
  --line:#cfcfcf;
  --nav-active:#333;
  --footer-bg:#ebebeb;
  --bar:#0d0d0d;
}
*{box-sizing:border-box;margin:0;padding:0}
html,body{width:689px;height:1200px;overflow:hidden;background:#fff}
body{position:relative;font-family:'Open Sans',Arial,sans-serif;color:var(--ink)}
.abs{position:absolute}

/* header */
.logo{left:76px;top:8px;font-size:23px;font-weight:700;color:var(--brand);letter-spacing:-.3px}
.top-links{left:513px;top:18px;font-size:8px;color:#222}
.top-links span{margin:0 5px;color:#999}

/* nav */
.nav{left:0;top:45px;width:689px;height:33px;background:var(--brand);display:flex;padding-left:76px}
.nav a{display:flex;align-items:center;justify-content:center;color:#fff;font-size:8.5px;text-decoration:none;border-right:1px solid rgba(0,0,0,.18);height:33px}
.nav a.active{background:var(--nav-active)}

/* hero */
.hero{left:0;top:78px;width:689px;height:257px;background:linear-gradient(90deg,#f3f3f3 0%,#ececec 45%,#e4e4e4 100%)}
.hero-photo{left:310px;top:78px;width:379px;height:257px;background:radial-gradient(ellipse at 45% 60%,#c9a88c 0%,#d9c4b3 35%,#e8e3df 70%,#eeeeee 100%)}
.join{left:75px;top:110px;width:181px;height:194px;background:var(--brand-soft);box-shadow:2px 3px 4px rgba(0,0,0,.35);text-align:center;color:#fff}
.join h2{margin-top:25px;font-size:14.5px;font-weight:700}
.join p{margin-top:8px;font-size:7px;color:#2a2a55}
.join .field{margin:13px auto 0;width:101px;height:13px;background:#fff;border-radius:2px;text-align:left;font-size:6px;color:#999;padding:2px 5px;box-shadow:0 1px 2px rgba(0,0,0,.3)}
.join .field+.field{margin-top:10px}
.join .register{margin:16px auto 0;width:73px;height:18px;background:#fff;color:var(--brand);font-weight:700;font-size:10px;line-height:18px;box-shadow:1px 2px 3px rgba(0,0,0,.35)}
.slide-arrow{top:192px;width:13px;height:30px;background:#777;color:#ddd;font-size:12px;line-height:30px;text-align:center}
.dots{left:327px;top:322px;display:flex;gap:2px}
.dots i{width:6px;height:6px;border-radius:50%;background:#666;display:block}
.dots i.on{background:var(--brand-soft)}

/* section titles */
.section-title{left:0;width:689px;text-align:center}
.section-title h3{font-size:14px;font-weight:700;color:var(--brand)}
.section-title p{font-size:7.5px;color:#444;margin-top:4px}

/* service cards */
.services{left:75px;top:425px;width:539px;height:215px;border:1px solid var(--line);display:flex}
.card{width:33.333%;border-right:1px solid var(--line);position:relative}
.card:last-child{border-right:none}
.card-photo{height:88px}
.card-label{height:20px;background:#262626;color:#fff;font-size:8px;text-align:center;line-height:20px}
.card-body{padding:12px 10px 0 10px;font-size:6px;color:var(--muted);line-height:11px}
.card-body ul{list-style:none;margin-top:2px;color:#444}
.card-body li{line-height:13.5px}
.card-body li::before{content:"›";color:var(--brand);font-weight:700;margin-right:3px}
.btn-start{position:absolute;left:50%;transform:translateX(-50%);top:193px;background:var(--brand);color:#fff;font-size:6px;font-weight:700;padding:1px 6px;letter-spacing:.2px}

/* steps boxes */
.steps{top:730px;width:233px;height:267px;border:1px solid var(--line)}
.steps-head{height:29px;background:var(--brand);color:#fff;font-size:13px;text-align:center;line-height:29px}
.steps-text{margin:8px 18px 0;font-size:6px;line-height:12px;color:var(--muted);text-align:justify}
.steps ul{list-style:none;margin:16px 0 0 61px}
.steps li{display:flex;align-items:center;height:26.3px;font-size:8px;color:#333}
.steps li svg{width:16px;height:16px;margin-right:5px;flex:none}

/* footer */
.footer{left:0;top:1025px;width:689px;height:146px;background:var(--footer-bg)}
.foot-col h4{font-size:8px;font-weight:400;color:#222;margin-bottom:5px}
.foot-col a{display:block;font-size:6.3px;color:#888;text-decoration:none;line-height:11.8px}
.social{left:593px;width:19px;height:19px}
.bottom-bar{left:0;top:1171px;width:689px;height:29px;background:var(--bar);color:#ddd;font-size:6.3px;text-align:center;line-height:29px}
</style>
</head>
<body>

<div class="abs logo">NestWatch</div>
<div class="abs top-links">Login ▾<span>|</span>Select Country ▾</div>

<nav class="abs nav">
  <a class="active" style="width:68px">Home</a>
  <a style="width:66px">About Us</a>
  <a style="width:64px">Services</a>
  <a style="width:81px">Enrollement</a>
  <a style="width:57px">FAQs</a>
  <a style="width:65px">Gallery</a>
  <a style="width:65px">Location</a>
  <a style="width:70px">Contact</a>
</nav>

<section>
  <div class="abs hero"></div>
  <div class="abs hero-photo" role="img" aria-label="Photo of a smiling mother holding her toddler and a teddy bear"></div>
  <div class="abs join">
    <h2>Join Now!!</h2>
    <p>Sign up to start a FREE search of our services</p>
    <div class="field">Name</div>
    <div class="field">Email Id</div>
    <div class="register">REGISTER</div>
  </div>
  <div class="abs slide-arrow" style="left:0">⟨</div>
  <div class="abs slide-arrow" style="left:676px">⟩</div>
  <div class="abs dots"><i></i><i></i><i class="on"></i><i></i><i></i></div>
</section>

<div class="abs section-title" style="top:367px"><h3>Services We Offer</h3><p>Your loved ones are in Good Hands</p></div>

<section class="abs services">
  <div class="card">
    <div class="card-photo" role="img" aria-label="Photo of smiling children lying on grass" style="background:linear-gradient(180deg,#cfe3f0 0%,#d9b9a0 45%,#c06a8a 70%,#3c5a1e 100%)"></div>
    <div class="card-label">Child Care</div>
    <div class="card-body">Lorem Ipsum is simply dummy text of the printing and typesetting industry.
      <ul><li>Lorem Ipsum has been the.</li><li>When an unknown printer took a galley.</li><li>Of type and scrambled it to make.</li></ul></div>
    <div class="btn-start">GET STARTED</div>
  </div>
  <div class="card">
    <div class="card-photo" role="img" aria-label="Photo of a caregiver smiling with an elderly man" style="background:linear-gradient(90deg,#b89a80 0%,#d8c2b0 45%,#cdb6a6 70%,#9a8f88 100%)"></div>
    <div class="card-label">Elder Care</div>
    <div class="card-body">Lorem Ipsum is simply dummy text of the printing and typesetting industry.
      <ul><li>Lorem Ipsum has been the.</li><li>When an unknown printer took a galley.</li><li>Of type and scrambled it to make.</li></ul></div>
    <div class="btn-start">GET STARTED</div>
  </div>
  <div class="card">
    <div class="card-photo" role="img" aria-label="Photo of a smiling woman with a golden retriever" style="background:linear-gradient(90deg,#e7d6bf 0%,#d9b98e 40%,#c79a5e 70%,#e6d2b0 100%)"></div>
    <div class="card-label">Pet Care</div>
    <div class="card-body">Lorem Ipsum is simply dummy text of the printing and typesetting industry.
      <ul><li>Lorem Ipsum has been the.</li><li>When an unknown printer took a galley.</li><li>Of type and scrambled it to make.</li></ul></div>
    <div class="btn-start">GET STARTED</div>
  </div>
</section>

<div class="abs section-title" style="top:672px"><h3>Its Easy</h3><p>Your loved ones are in Good Hands</p></div>

<svg width="0" height="0" style="position:absolute">
  <defs>
    <symbol id="i-mail" viewBox="0 0 16 16"><path d="M1 2l5 4" stroke="#3338dc" stroke-width="1.6" fill="none"/><rect x="4" y="6" width="11" height="8" fill="#3338dc"/><path d="M4 6l5.5 4L15 6" stroke="#fff" stroke-width="1" fill="none"/></symbol>
    <symbol id="i-search" viewBox="0 0 16 16"><circle cx="6.5" cy="6.5" r="4.6" stroke="#3338dc" stroke-width="1.8" fill="none"/><path d="M10 10l4.5 4.5" stroke="#3338dc" stroke-width="2.4" stroke-linecap="round"/></symbol>
    <symbol id="i-list" viewBox="0 0 16 16"><rect x="1.5" y="1.5" width="10" height="12" stroke="#3338dc" stroke-width="1.4" fill="none"/><path d="M4 5h5M4 8h5M4 11h3" stroke="#3338dc" stroke-width="1.2"/><circle cx="12.5" cy="12.5" r="3" fill="#3338dc"/></symbol>
    <symbol id="i-user" viewBox="0 0 16 16"><circle cx="8" cy="6" r="3.2" fill="#3338dc"/><path d="M2.5 15c0-3.5 2.5-5 5.5-5s5.5 1.5 5.5 5z" fill="#3338dc"/><circle cx="8" cy="7" r="6.3" stroke="#3338dc" stroke-width="1" fill="none"/></symbol>
    <symbol id="i-check" viewBox="0 0 16 16"><circle cx="8" cy="8" r="7.5" fill="#3338dc"/><path d="M4.3 8.3l2.5 2.5 5-5" stroke="#fff" stroke-width="1.8" fill="none"/></symbol>
  </defs>
</svg>

<section class="abs steps" style="left:97px">
  <div class="steps-head">Need Help ???</div>
  <p class="steps-text">Lorem Ipsum is simply dummy text of the printing and typesetting industry. Lorem Ipsum has been the industry's standard dummy text ever since the 1500s, when an unknown printer took a galley of type and scrambled it to make a type specimen book. It has survived not only five centuries, but also the leap into electronic typesetting, remaining essentially unchanged</p>
  <ul>
    <li><svg><use href="#i-mail"/></svg>Post your Requirements</li>
    <li><svg><use href="#i-search"/></svg>Search the Profiles</li>
    <li><svg><use href="#i-list"/></svg>List the Sitters</li>
    <li><svg><use href="#i-user"/></svg>Interview them</li>
    <li><svg><use href="#i-check"/></svg>Choose your Sitter</li>
  </ul>
</section>

<section class="abs steps" style="left:359px">
  <div class="steps-head">Need Job ???</div>
  <p class="steps-text">Lorem Ipsum is simply dummy text of the printing and typesetting industry. Lorem Ipsum has been the industry's standard dummy text ever since the 1500s, when an unknown printer took a galley of type and scrambled it to make a type specimen book. It has survived not only five centuries, but also the leap into electronic typesetting, remaining essentially unchanged</p>
  <ul>
    <li><svg><use href="#i-mail"/></svg>Post your Profile</li>
    <li><svg><use href="#i-search"/></svg>Search the Vacancies</li>
    <li><svg><use href="#i-list"/></svg>List the Vacancies</li>
    <li><svg><use href="#i-user"/></svg>Get interviewd</li>
    <li><svg><use href="#i-check"/></svg>Join the Family</li>
  </ul>
</section>

<footer>
  <div class="abs footer"></div>
  <div class="abs foot-col" style="left:78px;top:1055px"><h4>About Us</h4><a>Investor Relations</a><a>Help</a><a>Safety Center</a><a>Gallery</a><a>Careers</a><a>Contact</a></div>
  <div class="abs foot-col" style="left:210px;top:1054px"><h4>For Children</h4><a>Child Care</a><a>Babysitters</a><a>Nannies</a><a>Special Needs Care</a><a>Camps</a><a>More Services</a></div>
  <div class="abs foot-col" style="left:345px;top:1054px"><h4>For Adults &amp; Seniors</h4><a>Senior Care</a><a>Home Care</a><a>Senior Housing</a><a>Senior Care Jobs</a><a>Senior Care Planning</a><a>More Services</a></div>
  <div class="abs foot-col" style="left:480px;top:1054px"><h4>For Pets</h4><a>Pet Care</a><a>Pet Sitters</a><a>Dog Walkers</a><a>Pet Sitting</a><a>Pet Care Jobs</a><a>More Services</a></div>
  <div class="abs social" style="top:1057px;background:#d9493a"></div>
  <div class="abs social" style="top:1079px;background:#3aa3de"></div>
  <div class="abs social" style="top:1101px;background:#c8302a"></div>
  <div class="abs social" style="top:1123px;background:#3b5a9a"></div>
  <div class="abs bottom-bar">By using this site you agree to the Terms of Use. See our Privacy Policy. ©2014 NestWatch Incorporated. All Rights Reserved.</div>
</footer>

</body>
</html>
```